New Year's card HTML

can you produce a best new years wishes 2018 design in HTML for our website as what I would like to send by email towards my network of candidates / customers ...

It must be wow, inspiring , design, meaningfull... MMM those people care about me, or those people will help me to go the extra mile, to help me to achieve my career goals, Your best move, enhance my possibilities, bring the love back

Target Market(s)

CEo's / CMO's/ HRDirectors network of 450k

Coding

Coded - Design and coding required

Number of Pages Required

1 page

Colors

Designer to choose colors to be used in the design.

Requirements
Must have
• Logo / visual / website adress www.moravintel.com and a call to action
Should not have
• no sound as our business is confidential

```html
<!DOCTYPE html>
<html lang="en">
<head>
<meta charset="utf-8">
<title>Happy New Year 2018 – Moravintel</title>
<link rel="stylesheet" href="https://fonts.googleapis.com/css2?family=Cinzel:wght@400;500&family=Nunito:wght@600&display=swap">
<style>
  :root {
    --deep-violet: #3a0f6e;
    --violet: #5a1e9a;
    --royal: #4b1a8c;
    --ember: #e8262e;
    --magenta: #d0309a;
    --electric: #3d4ef0;
    --white: #ffffff;
    --lilac: #e7d6ff;
    --rose-shadow: #ff4f8d;
    --button-text: #4a1b72;
    --rule: rgba(255, 255, 255, 0.85);
  }
  * { box-sizing: border-box; margin: 0; padding: 0; }
  html, body { width: 929px; height: 1200px; overflow: hidden; background: var(--deep-violet); }
  .card {
    position: relative;
    width: 929px;
    height: 1200px;
    overflow: hidden;
    background:
      radial-gradient(ellipse 520px 420px at 60px 1130px, rgba(232, 38, 46, 0.95), rgba(200, 30, 80, 0.55) 45%, transparent 75%),
      radial-gradient(ellipse 700px 500px at 500px 300px, var(--violet), transparent 80%),
      linear-gradient(180deg, var(--royal) 0%, var(--violet) 45%, #6a1c8a 75%, #8a1f5a 100%);
    font-family: "Cinzel", "Times New Roman", serif;
    color: var(--white);
  }
  .globe {
    position: absolute;
    left: 320px;
    top: 475px;
    width: 860px;
    height: 860px;
  }
  .brand {
    position: absolute;
    top: 68px;
    left: 0;
    width: 100%;
    text-align: center;
    font-size: 52px;
    font-weight: 400;
    letter-spacing: 2px;
    line-height: 1;
  }
  .greeting {
    position: absolute;
    top: 196px;
    left: 100px;
    width: 770px;
    height: 119px;
    border-top: 2px solid var(--rule);
    border-bottom: 2px solid var(--rule);
    display: flex;
    align-items: center;
    justify-content: center;
  }
  .greeting::before, .greeting::after {
    content: "";
    position: absolute;
    left: 0;
    right: 0;
    height: 1px;
    background: var(--rule);
  }
  .greeting::before { top: 8px; }
  .greeting::after { bottom: 8px; }
  .greeting h1 {
    font-size: 78px;
    font-weight: 400;
    letter-spacing: 3px;
    line-height: 1;
  }
  .year {
    position: absolute;
    top: 345px;
    left: 0;
    width: 929px;
    text-align: center;
    font-size: 300px;
    font-weight: 500;
    line-height: 1;
    letter-spacing: 2px;
    color: var(--white);
    background: linear-gradient(180deg, var(--lilac) 0%, var(--white) 45%);
    -webkit-background-clip: text;
    background-clip: text;
    -webkit-text-fill-color: transparent;
    filter: drop-shadow(7px 6px 0 var(--rose-shadow));
  }
  .cta {
    position: absolute;
    top: 670px;
    left: 198px;
    width: 546px;
    height: 98px;
    border-radius: 49px;
    background: linear-gradient(180deg, #ffffff 0%, #f1eef4 60%, #dcd6e2 100%);
    box-shadow: 0 6px 14px rgba(30, 0, 50, 0.35);
    display: flex;
    align-items: center;
    justify-content: center;
    font-family: "Nunito", "Helvetica", sans-serif;
    font-weight: 600;
    font-size: 33px;
    letter-spacing: 0.5px;
    color: var(--button-text);
    text-decoration: none;
  }
</style>
</head>
<body>
  <main class="card">
    <svg class="globe" viewBox="0 0 860 860" role="img" aria-label="Glowing digital globe made of connected network lines">
      <defs>
        <radialGradient id="globe-fill" cx="0.4" cy="0.35" r="0.7">
          <stop offset="0" stop-color="#7a4bff"/>
          <stop offset="0.45" stop-color="#5a3cf0"/>
          <stop offset="0.75" stop-color="#c03cc8"/>
          <stop offset="1" stop-color="#f04a8a"/>
        </radialGradient>
      </defs>
      <circle cx="430" cy="430" r="430" fill="url(#globe-fill)" opacity="0.9"/>
    </svg>

    <div class="brand">MORAVINTEL</div>

    <header class="greeting">
      <h1>HAPPY NEW YEAR</h1>
    </header>

    <div class="year">2018</div>

    <a class="cta" href="https://www.moravintel.com">VISIT OUR WEBSITE</a>
  </main>
</body>
</html>
```